Larkspur Talent IT Recruiting firm needs a business card design for Recruiters, Sourcers, and Account

We need business cards that allow us to change all contact info, names, titles (Recruiter, Sourcer, Account Manager, Director, CEO, etc) per person since we have three offices, in three cities, Phoenix, Austin, and Las Vegas. We do recruiting and contractors for IT positions (Developers, Architects, Software Engineers, Security Engineers, Help Desk, DBAs, PMs, Scrum Masters, etc.) Our client companies are very diverse from Meridian 100 to silicone Valley type start-ups.

So, while we what hip, techie, and quirky, it still needs to be professional. Primary color we use is blue, with silver as a secondary color.

Target Market(s)

IT, Technology

Industry/Entity Type

Business

Contact Information for Business Card

Company name: Larkspur Talent, Inc.
Website: www.larkspurtalent.example
Logos for Careerloop, Blipster, and Myriada

Name, Title, Office Number, Cell Number, email

Font styles to use
Serif
Sans Serif

Colors
0455a3
d5d5d5

Requirements
Nice to have
• The grey I selected below is not necessary - but, would like silver included. I included a card design (File 3: LTI early trial example.jpg) that I had started on. It's very rough, and not quite what we're looking for, but what we did like is the logo, big, maybe a bit faded, off center, goes out of frame, etc. Still looking for other ideas - you are the pros! But, just an idea of a design element we liked.

```html
<!DOCTYPE html>
<html lang="en">
<head>
<meta charset="utf-8">
<title>Larkspur Talent — Business Cards</title>
<link rel="stylesheet" href="https://fonts.googleapis.com/css2?family=Cinzel:wght@400;600&family=Montserrat:wght@400;500&display=swap">
<style>
  :root {
    --brand-blue: #0455a3;
    --bright-blue: #1f8fd6;
    --light-blue: #3bb0e6;
    --silver: #d5d5d5;
    --ink: #1d1d1f;
    --paper: #ffffff;
    --page: #eceef1;
  }
  * { box-sizing: border-box; margin: 0; padding: 0; }
  html, body { width: 1200px; height: 900px; overflow: hidden; }
  body { background: var(--page); position: relative; font-family: "Cinzel", serif; color: var(--ink); }

  .card {
    position: absolute; width: 700px; height: 400px;
    background: var(--paper); overflow: hidden;
    box-shadow: 0 8px 24px rgba(0,0,0,.18);
  }
  .card--front { left: 140px; top: 22px; }
  .card--back { left: 360px; top: 470px; }

  .emblem-area {
    position: absolute; border-radius: 50%;
    background: radial-gradient(circle at 70% 30%, var(--light-blue), var(--brand-blue) 75%);
  }
  .card--front .emblem-area--left { width: 300px; height: 300px; left: -170px; top: 110px; }
  .card--front .emblem-area--right { width: 200px; height: 200px; right: -110px; top: -70px; }
  .card--back .emblem-area--left { width: 340px; height: 340px; left: -180px; top: 100px; }
  .card--back .emblem-area--right { width: 220px; height: 220px; right: -110px; top: -100px; }

  .wordmark { position: absolute; display: flex; align-items: center; gap: 12px; white-space: nowrap; }
  .wordmark__dot { width: 30px; height: 30px; border-radius: 50%; background: var(--brand-blue); flex: none; }
  .wordmark__name { font-family: "Cinzel", serif; font-weight: 400; color: var(--ink); letter-spacing: 3px; line-height: 1; }
  .card--front .wordmark { left: 160px; top: 120px; }
  .card--front .wordmark__name { font-size: 36px; }
  .card--back .wordmark { left: 170px; top: 60px; }
  .card--back .wordmark__name { font-size: 36px; }

  .tagline { position: absolute; font-size: 17px; letter-spacing: 4px; color: var(--ink); white-space: nowrap; }
  .card--front .tagline { left: 0; right: 0; top: 200px; text-align: center; }
  .card--back .tagline { left: 200px; top: 118px; font-size: 16px; }

  .band { position: absolute; left: 0; right: 0; bottom: 0; background: linear-gradient(90deg, var(--brand-blue), var(--bright-blue)); }
  .card--front .band { height: 40px; display: flex; align-items: center; justify-content: center; }
  .card--back .band { height: 16px; }
  .band__url { font-family: "Montserrat", sans-serif; font-size: 10px; letter-spacing: 3px; color: var(--paper); text-transform: uppercase; }

  .person { position: absolute; left: 200px; top: 158px; width: 330px; text-align: center; border-bottom: 1px solid var(--bright-blue); padding-bottom: 6px; }
  .person__name { font-size: 18px; font-weight: 600; letter-spacing: 1px; white-space: nowrap; }
  .person__title { font-family: "Montserrat", sans-serif; font-size: 9px; letter-spacing: 2px; color: var(--bright-blue); text-transform: uppercase; }

  .contacts { position: absolute; left: 172px; top: 218px; display: flex; gap: 10px; }
  .social { display: flex; flex-direction: column; gap: 12px; padding-top: 10px; }
  .social__row { display: flex; align-items: center; justify-content: flex-end; gap: 6px; font-size: 10px; font-weight: 600; white-space: nowrap; }
  .social__net { font-family: "Montserrat", sans-serif; font-weight: 500; font-size: 8px; color: var(--brand-blue); width: 46px; text-align: right; }
  .social__mark { width: 16px; height: 16px; background: var(--brand-blue); flex: none; }
  .divider { width: 1px; background: var(--bright-blue); }
  .details { display: flex; flex-direction: column; gap: 7px; }
  .details__row { display: flex; align-items: center; gap: 8px; font-family: "Cinzel", serif; font-size: 10.5px; white-space: nowrap; }
  .details__icon { width: 12px; height: 12px; fill: var(--brand-blue); flex: none; }
</style>
</head>
<body>

<section class="card card--front" aria-label="Business card front">
  <div class="emblem-area emblem-area--left" role="img" aria-label="Large cropped brand emblem in blue gradient"></div>
  <div class="emblem-area emblem-area--right" role="img" aria-label="Large cropped brand emblem in blue gradient"></div>
  <div class="wordmark">
    <span class="wordmark__dot"></span>
    <span class="wordmark__name">Larkspur Talent</span>
  </div>
  <p class="tagline">Rising to the Challenge</p>
  <div class="band"><span class="band__url">www.larkspurtalent.example</span></div>
</section>

<section class="card card--back" aria-label="Business card back">
  <div class="emblem-area emblem-area--left" role="img" aria-label="Large cropped brand emblem in blue gradient"></div>
  <div class="emblem-area emblem-area--right" role="img" aria-label="Large cropped brand emblem in blue gradient"></div>
  <div class="wordmark">
    <span class="wordmark__dot"></span>
    <span class="wordmark__name">Larkspur Talent</span>
  </div>
  <p class="tagline">Rising to the Challenge</p>

  <div class="person">
    <p class="person__name">Marcus D. Whitfield</p>
    <p class="person__title">Director</p>
  </div>

  <div class="contacts">
    <div class="social">
      <div class="social__row">Marcus D. Whitfield <span class="social__net">Myriada</span><span class="social__mark"></span></div>
      <div class="social__row">Marcus D. Whitfield <span class="social__net">Blipster</span><span class="social__mark"></span></div>
      <div class="social__row">Marcus D. Whitfield <span class="social__net">Careerloop</span><span class="social__mark"></span></div>
    </div>
    <div class="divider"></div>
    <div class="details">
      <p class="details__row">
        <svg class="details__icon" viewBox="0 0 12 12" aria-hidden="true"><rect x="3" y="0" width="6" height="12" rx="1"/><rect x="4" y="1.5" width="4" height="7.5" fill="#fff"/></svg>
        555-014-0201
      </p>
      <p class="details__row">
        <svg class="details__icon" viewBox="0 0 12 12" aria-hidden="true"><path d="M2.5 0.5l2 2.5-1.2 1.3c.8 1.7 2 2.9 3.7 3.7L8.3 6.8l2.7 2-1.2 2.4C5 10.8 1.2 7 .5 2z"/></svg>
        555-014-0200
      </p>
      <p class="details__row">
        <svg class="details__icon" viewBox="0 0 12 12" aria-hidden="true"><circle cx="6" cy="6" r="5.5"/><path d="M.5 6h11M6 .5c-2.5 3-2.5 8 0 11M6 .5c2.5 3 2.5 8 0 11" stroke="#fff" stroke-width=".8" fill="none"/></svg>
        www.larkspurtalent.example
      </p>
      <p class="details__row">
        <svg class="details__icon" viewBox="0 0 12 12" aria-hidden="true"><rect x="0" y="2" width="12" height="8"/><path d="M0 2l6 4.5L12 2" stroke="#fff" stroke-width=".9" fill="none"/></svg>
        m.whitfield@larkspurtalent.example
      </p>
    </div>
  </div>

  <div class="band"></div>
</section>

</body>
</html>
```